Martial Arts Website

Redevelopment of existing martial arts website.

The academy teaches traditional shaolin martial arts, including Shaolin Kung Fu, Wu Shu, Tai Chi, Qigong and Wing Chun and the site needs to reflect the traditional roots (eg, no tacky boxing imagery)

Existing website is www.copperlantern.com.au to get a feel for the desired color scheme (black, green and red). The exact colors can be tweaked though. Please only reuse the logo and font (Karate) - there isnt anything else from the current design that needs to remain.

The current website includes links to a ClipHarbor channel that includes demonstrations of the training conducted to better guide the design.

The new website site map will be:
1. Home
2. Programs - summary page describing each form of training
a. Tiny Otters
b. Kids Kung Fu
c. Youth Kung Fu
d. Adults Kung Fu
e. Wing Chun
f. Tai Chi & Qigong
g. Weaponry Classes
h. 72 Arts of Shaolin Conditioning Program
i. Acrobatics and Wu Shu
j. Fitness Boxing
3. Timetable
4. Coaches - summary page describing all coaches
a. Sifu (Master)
b. Sihing Kit
c. Sihing Sam
d. Sihing Marcus
X. ... up to 10 or so coaches
5. Member Zone
6. Contact Us
Updates

Logo now attached to brief - sorry I only have it in PDF

Just to clarify, I am only expecting a PSD design - no HTML required

Reason: Thanks for the designs, we love a lot of them just require a little extra time to tweak the designs and establish the potential. Thanks for your understanding and efforts.

Target Market(s)

Parents, teenagers, young adults, adults, elderly

Industry/Entity Type

Training

Requirements
Must have
• Chinese kung fu dragon imagery throughout the background
Links to Chatterly and ClipHarbor channel
Promo/icon in the header "Try 2 free classes now"
Home page should include an embedded ClipHarbor video

```html
<!DOCTYPE html>
<html lang="en">
<head>
<meta charset="utf-8">
<title>Copper Lantern Martial Arts Academy</title>
<link rel="stylesheet" href="https://fonts.googleapis.com/css2?family=Cormorant+Garamond:wght@500;600&family=Ubuntu+Condensed&family=Lato:wght@400&display=swap">
<style>
:root{
  --green-deep:#0f5a0c;
  --green-mid:#1f8a12;
  --green-bright:#2fb51c;
  --green-menu:#0b5d07;
  --green-text:#4cc92a;
  --menu-ink:#0a2a05;
  --black:#000;
  --ink:#ffffff;
  --muted:#8c8c8c;
  --rule:#333;
}
*{margin:0;padding:0;box-sizing:border-box}
html,body{width:932px;height:1200px;overflow:hidden}
body{position:relative;background:linear-gradient(180deg,var(--green-mid) 0%,var(--green-deep) 45%,#0d4a0a 80%);font-family:"Lato",sans-serif;color:var(--ink)}
.site-title{position:absolute;top:44px;font-family:"Cormorant Garamond",serif;font-weight:500;font-size:25px;color:#f1f5e9;letter-spacing:.5px}
.site-title.left{right:580px}
.site-title.right{left:527px}
.frame{position:absolute;left:14px;top:97px;width:905px;height:876px;background:var(--black);border-radius:6px 6px 0 0}
.nav{position:absolute;left:23px;top:105px;width:885px;height:59px;background:linear-gradient(180deg,#27b41a 0%,#16960c 55%,#0f7d08 100%);border-radius:4px}
.nav a{position:absolute;top:24px;font-family:"Ubuntu Condensed",sans-serif;font-size:15px;color:var(--menu-ink);text-decoration:none;text-transform:uppercase}
.nav a.small{font-size:13px;top:25px}
.nav .active{position:absolute;left:104px;top:9px;width:106px;height:50px;background:var(--green-menu);border-radius:6px 6px 0 0}
.nav a.on{color:var(--green-text)}
.logo{position:absolute;left:364px;top:18px;width:160px;height:160px;border-radius:50%;background:#0a1f08;border:6px solid #3fc22c;z-index:3}
.hero{position:absolute;left:25px;top:167px;width:881px;height:327px;background:linear-gradient(180deg,#8a6c4f 0%,#c9c2b7 35%,#bfa59a 65%,#c86a55 100%);border-radius:0 0 4px 4px}
.dropdown{position:absolute;left:127px;top:160px;width:236px;height:118px;background:var(--green-menu);border-radius:0 6px 6px 6px;z-index:2;display:grid;grid-template-columns:102px 120px;grid-auto-rows:24.5px;padding:10px 0 0 19px}
.dropdown span{font-family:"Ubuntu Condensed",sans-serif;font-size:13px;color:var(--green-text)}
.content{position:absolute;left:25px;top:494px;width:881px;height:479px;border-left:1px solid var(--rule);border-right:1px solid var(--rule)}
.main{position:absolute;left:17px;top:22px;width:571px;height:438px;overflow:hidden}
.main h2{font-family:"Ubuntu Condensed",sans-serif;font-weight:400;font-size:18px;color:var(--green-text);margin-bottom:4px}
.main h2.second{margin-top:16px;font-size:20px}
.main p{font-size:11.3px;line-height:16.4px;text-align:justify;margin-bottom:5px}
.side-photo{position:absolute;left:599px;top:14px;width:271px;height:189px;border-radius:6px;background:linear-gradient(180deg,#8c8579 0%,#a9786f 55%,#9a6a63 100%)}
.footer{position:absolute;left:0;top:973px;width:932px;height:227px;background:var(--black)}
.links{position:absolute;top:30px;list-style:none}
.links li{font-size:11.5px;height:27.3px;padding-left:14px;position:relative}
.links li::before{content:"";position:absolute;left:0;top:3px;border-left:5px solid #777;border-top:4px solid transparent;border-bottom:4px solid transparent}
.footer-logo{position:absolute;left:714px;top:16px;width:110px;height:110px;border-radius:50%;background:#0a1f08;border:5px solid #3fc22c}
.copy{position:absolute;left:44px;top:170px;font-size:11px;color:var(--muted)}
</style>
</head>
<body>
<div class="site-title left">Copper Lantern</div>
<div class="site-title right">Martial Arts Academy</div>
<div class="frame"></div>
<nav class="nav">
  <div class="active"></div>
  <a style="left:46px">Home</a>
  <a class="on" style="left:122px">Programs</a>
  <a style="left:226px">Timetable</a>
  <a class="small" style="left:553px">Coaches</a>
  <a class="small" style="left:634px">Member Zone</a>
  <a class="small" style="left:749px">Contact Us</a>
</nav>
<div class="logo" role="img" aria-label="Copper Lantern academy emblem"></div>
<div class="hero" role="img" aria-label="Tai chi class training in a sports hall"></div>
<div class="dropdown">
  <span>Tiny Otters</span><span>Wing Chun</span>
  <span>Kids Kung Fu</span><span>Tai Chi &amp; Qigong</span>
  <span>Youth Kung Fu</span><span>Weaponry Classes</span>
  <span>Adults Kung Fu</span><span>72 Arts of Shaolin</span>
</div>
<section class="content">
  <div class="main">
    <h2>About Us</h2>
    <p>Lorem ipsum dolor sit amet, consectetuer adipiscing elit. Nam cursus. Morbi ut mi. Nullam enim leo, egestas id, condimentum at, laoreet mattis, massa. Sed eleifend nonummy diam. Praesent mauris ante, elementum et, bibendum at, posuere sit amet, nibh. Duis tincidunt lectus quis dui viverra vestibulum.</p>
    <p>Suspendisse vulputate aliquam dui. Nulla elementum dui ut augue. Aliquam vehicula mi at mauris. Maecenas placerat, nisl at consequat rhoncus, sem nunc gravida justo, quis eleifend arcu velit quis lacus. Morbi magna magna, tincidunt a, mattis non, imperdiet vitae, tellus. Sed odio est, auctor ac, sollicitudin in, consequat vitae, orci. Fusce id felis. Vivamus sollicitudin metus eget eros.</p>
    <p>Lorem ipsum dolor sit amet, consectetuer adipiscing elit. Nam cursus. Morbi ut mi. Nullam enim leo, egestas id, condimentum at, laoreet mattis, massa. Sed eleifend nonummy diam. Praesent mauris ante, elementum et, bibendum at, posuere sit amet, nibh. Duis tincidunt lectus quis dui viverra vestibulum.</p>
    <p>Suspendisse vulputate aliquam dui. Nulla elementum dui ut augue. Aliquam vehicula mi at mauris. Maecenas placerat, nisl at consequat rhoncus, sem nunc gravida justo, quis eleifend arcu velit quis lacus. Morbi magna magna, tincidunt a, mattis non, imperdiet vitae, tellus. Sed odio est, auctor ac, sollicitudin in, consequat vitae, orci. Fusce id felis. Vivamus sollicitudin metus eget eros.</p>
    <h2 class="second">Heading</h2>
    <p>Lorem ipsum dolor sit amet, consectetuer adipiscing elit. Nam cursus. Morbi ut mi. Nullam enim leo, egestas id, condimentum at, laoreet mattis, massa. Sed eleifend nonummy diam. Praesent mauris ante, elementum et, bibendum at, posuere sit amet, nibh. Duis tincidunt lectus quis dui viverra vestibulum.</p>
    <p>Suspendisse vulputate aliquam dui. Nulla elementum dui ut augue. Aliquam vehicula mi at mauris. Maecenas placerat, nisl at consequat rhoncus, sem nunc gravida justo, quis eleifend arcu velit quis lacus. Morbi magna magna, tincidunt a, mattis non, imperdiet vitae, tellus. Sed odio est, auctor ac, sollicitudin in, consequat vitae, orci. Fusce id</p>
  </div>
  <div class="side-photo" role="img" aria-label="Young student kneeling in a kung fu stance"></div>
</section>
<footer class="footer">
  <ul class="links" style="left:43px"><li>Home</li><li>Programs</li><li>Timtable</li><li>Coaches</li></ul>
  <ul class="links" style="left:153px"><li>Support</li><li>FAQ</li><li>Newsletters</li><li>Social Media</li></ul>
  <ul class="links" style="left:275px"><li>Tiny Otters</li><li>Kids Kung Fu</li><li>Youth Kung Fu</li><li>Adults Kung Fu</li></ul>
  <ul class="links" style="left:416px"><li>Wing Chun</li><li>Tai Chi &amp; Qigong</li><li>Weaponry Classes</li><li>72 Arts of Shaolin</li></ul>
  <div class="footer-logo" role="img" aria-label="Copper Lantern academy emblem"></div>
  <div class="copy">© 2012 Copper Lantern Academy &nbsp;|&nbsp; All right reserved</div>
</footer>
</body>
</html>
```